Banner for construction site to identify developer

we need a 4 foot by 8 foot banner to hang on the fence of a residential townhome development in Phoenix, Arizona that identifies Tolvane Holdings as the company behind the development/project. Also needs to include the logo, phone number, and web address. Would like to stick with the blue colors provided in the attached logo. The blues should stay the same but the letters in the logo can change to another color if necessary. Feel free to use "Tolvane Holdings" in place of "Tolvane Holdings Group". Looking for use of colors/design to take up space so banner is not just text with a logo.

Target Market(s)

drive by traffic looking at the site

Industry/Entity Type

Real Estate

Colors
0054AA
0677BA
7BADD7
CADEEF
E8F1F8

Requirements
Must have
• company name, phone number and web address

```html
<!DOCTYPE html>
<html lang="en">
<head>
<meta charset="utf-8">
<title>Tolvane Holdings – Site Banner</title>
<link rel="stylesheet" href="https://fonts.googleapis.com/css2?family=Open+Sans:wght@400;700;800&display=swap">
<style>
  :root {
    --page-bg: #c4c4c4;
    --banner-white: #ffffff;
    --brand-blue: #1d79b4;
    --brand-blue-deep: #15609a;
    --brand-blue-light: #1ca6dc;
    --ribbon-dark: #3d3d40;
    --ink-dark: #333336;
    --divider: #d6d6d6;
  }
  * { box-sizing: border-box; margin: 0; padding: 0; }
  html, body {
    width: 913px; height: 1200px; overflow: hidden;
    background: var(--page-bg);
    font-family: "Open Sans", Arial, sans-serif;
  }
  .canvas { position: relative; width: 913px; height: 1200px; }
  .banner {
    position: absolute; left: 26px; top: 385px;
    width: 860px; height: 430px;
    background: var(--banner-white);
    box-shadow: 6px 10px 14px rgba(0,0,0,0.35);
    overflow: hidden;
  }
  .banner__photo-band {
    position: absolute; left: 0; top: 0; width: 100%; height: 212px;
    background: linear-gradient(100deg, var(--brand-blue) 0%, #2385c0 45%, var(--brand-blue-deep) 75%, #1f7db8 100%);
  }
  .banner__headline {
    position: absolute; left: 0; top: 44px; width: 100%;
    text-align: center; color: var(--banner-white);
    font-weight: 800; font-size: 38px; letter-spacing: -0.3px; line-height: 1;
  }
  .banner__ribbon { position: absolute; left: 0; top: 0; width: 860px; height: 280px; }
  .banner__name {
    position: absolute; left: 0; top: 130px; width: 100%;
    text-align: center; color: var(--banner-white);
    font-weight: 800; font-size: 62px; letter-spacing: -1px; line-height: 1.1;
  }
  .brand-lockup {
    position: absolute; left: 45px; top: 296px;
    display: flex; align-items: center; gap: 12px;
  }
  .brand-lockup__square { width: 40px; height: 40px; background: var(--brand-blue-light); }
  .brand-lockup__name {
    color: var(--ink-dark); font-weight: 800; font-size: 25px; line-height: 1.1; letter-spacing: -0.5px;
  }
  .contact-divider {
    position: absolute; left: 337px; top: 288px; width: 1px; height: 96px; background: var(--divider);
  }
  .contact-phone {
    position: absolute; left: 358px; top: 286px;
    display: flex; align-items: center; gap: 6px;
    color: var(--ink-dark); font-weight: 800; font-size: 48px; letter-spacing: -1px; line-height: 1;
  }
  .contact-phone__icon { width: 40px; height: 40px; flex: none; }
  .contact-web {
    position: absolute; left: 360px; top: 350px;
    color: var(--ink-dark); font-weight: 800; font-size: 30px; letter-spacing: 1px; line-height: 1;
  }
  .contact-web__name { color: var(--brand-blue-light); }
</style>
</head>
<body>
<main class="canvas">
  <section class="banner">
    <div class="banner__photo-band" role="img" aria-label="Townhome development photo tinted in brand blue"></div>
    <h2 class="banner__headline">THIS PROJECT IS DEVELOPED BY</h2>
    <svg class="banner__ribbon" viewBox="0 0 860 280" aria-hidden="true">
      <defs>
        <filter id="ribbon-shadow" x="-10%" y="-10%" width="120%" height="140%">
          <feDropShadow dx="0" dy="8" stdDeviation="7" flood-color="#000" flood-opacity="0.35"/>
        </filter>
      </defs>
      <polygon points="42,120 811,120 756,251 97,251" fill="var(--ribbon-dark)" filter="url(#ribbon-shadow)"/>
    </svg>
    <h1 class="banner__name">Tolvane Holdings</h1>

    <div class="brand-lockup">
      <span class="brand-lockup__square"></span>
      <span class="brand-lockup__name">Tolvane Holdings<br>Group</span>
    </div>

    <div class="contact-divider"></div>

    <div class="contact-phone">
      <svg class="contact-phone__icon" viewBox="0 0 40 40" aria-hidden="true">
        <circle cx="20" cy="20" r="19" fill="var(--brand-blue-light)"/>
        <circle cx="20" cy="20" r="13" fill="#fff"/>
        <path d="M14 12c1-1 2-1 3 0l2 3c.6 1 .3 1.8-.5 2.4l-1 .8c.8 2 2.3 3.5 4.3 4.3l.8-1c.6-.8 1.4-1.1 2.4-.5l3 2c1 1 1 2 0 3l-1.5 1.5c-5 1-13-7-12-12z" fill="var(--brand-blue-light)"/>
      </svg>
      <span>234 5550 1472</span>
    </div>

    <p class="contact-web">www.<span class="contact-web__name">TolvaneHoldings</span>.com</p>
  </section>
</main>
</body>
</html>
```